Business Card for Multi-Brand Sportswear Company

We are looking for a business card which represents our company and the multiple brands within it.

The company: Fen Athletics (LTD)
The brands: Fen, TavaPuni, ElmStretch, Grit and Rain

Employees using these cards would be representing Fen Athletics, rather than any of the individual brands. You will see a current design within the uploaded files, to give some inspiration. The actual text of the brands is not necessary, but the logos should be on there is some format.

Our creative minds on this are stretched, so we are looking for someone to make this their own, and show us what a good business card should look like.

We may like to get these printed with spot gloss, so keep that in mind with your designs.

www.fenathletics.co.uk

Industry/Entity Type

Business

Contact Information for Business Card

Leo Pemberton-Hale
Operations Manager
(+44) 1632 960 418
Leo@fenathletics.co.uk
www.fenathletics.co.uk

Font styles to use
Sans Serif
Other font styles liked:
• Eurostile

Colors
ffffff

Requirements
Nice to have
• Dark (black) background

```html
<!DOCTYPE html>
<html lang="en">
<head>
<meta charset="utf-8">
<title>Fen Athletics Business Card</title>
<link rel="stylesheet" href="https://fonts.googleapis.com/css2?family=Saira:wght@400;600;700&display=swap">
<style>
  :root {
    --stage: #3a3330;
    --card-black: #141414;
    --card-black-deep: #0c0c0c;
    --gloss: #262626;
    --red: #d8221c;
    --white: #ffffff;
    --muted: #d9d9d9;
  }
  * { margin: 0; padding: 0; box-sizing: border-box; }
  html, body {
    width: 1200px; height: 716px; overflow: hidden;
    background: var(--stage);
    font-family: "Saira", "Helvetica Neue", Arial, sans-serif;
  }
  .canvas {
    position: relative; width: 1200px; height: 716px;
    display: flex; align-items: center; justify-content: center; gap: 50px;
  }
  .card {
    position: relative; width: 540px; height: 320px;
    background: linear-gradient(160deg, var(--card-black) 0%, var(--card-black-deep) 100%);
    overflow: hidden;
    box-shadow: 0 10px 28px rgba(0,0,0,.45);
  }

  /* Back face: spot gloss brand name */
  .card-back .gloss-mark {
    position: absolute; left: 0; right: 0; top: 118px;
    text-align: center;
  }
  .gloss-mark .brand-name {
    font-weight: 700; font-size: 46px; letter-spacing: 2px;
    color: var(--gloss); text-transform: uppercase; line-height: 1;
  }
  .gloss-mark .tagline {
    margin-top: 6px; font-size: 11px; letter-spacing: 4px;
    color: var(--gloss); text-transform: uppercase;
  }

  /* Front face */
  .card-front .swoosh { position: absolute; inset: 0; }
  .person { position: absolute; left: 30px; top: 26px; }
  .person .name { color: var(--red); font-weight: 700; font-size: 19px; line-height: 1.1; }
  .person .role { color: var(--white); font-size: 12px; margin-top: 2px; }

  .front-mark { position: absolute; right: 30px; top: 88px; text-align: right; }
  .front-mark .brand-name {
    font-weight: 700; font-size: 30px; letter-spacing: 1px;
    color: var(--white); text-transform: uppercase; line-height: 1;
  }
  .front-mark .tagline {
    margin-top: 4px; font-size: 8px; letter-spacing: 3px;
    color: var(--white); text-transform: uppercase;
  }

  .contacts { position: absolute; left: 30px; top: 100px; list-style: none; }
  .contacts li {
    display: flex; align-items: center; gap: 8px;
    color: var(--white); font-size: 12.5px; margin-bottom: 5px;
  }
  .contacts svg { width: 13px; height: 13px; fill: var(--red); flex: none; }

  .brand-row {
    position: absolute; left: 30px; top: 150px;
    display: flex; align-items: center; gap: 12px; list-style: none;
  }
  .brand-row li {
    display: flex; align-items: center; gap: 4px;
    color: var(--white); font-size: 10px; font-weight: 600;
  }
  .brand-row .dot { width: 8px; height: 8px; background: var(--red); }

  .web {
    position: absolute; right: 150px; top: 168px;
    display: flex; align-items: center; gap: 5px;
    color: var(--white); font-size: 12.5px;
  }
  .web .at { color: var(--red); font-weight: 700; }

  .address {
    position: absolute; right: 26px; bottom: 22px; text-align: right;
    color: var(--white); font-size: 13px; line-height: 1.35;
  }
</style>
</head>
<body>
<main class="canvas">

  <section class="card card-back" aria-label="Card back">
    <div class="gloss-mark">
      <div class="brand-name">Fen Athletics</div>
      <div class="tagline">Performance Wear</div>
    </div>
  </section>

  <section class="card card-front" aria-label="Card front">
    <svg class="swoosh" viewBox="0 0 540 320" preserveAspectRatio="none" aria-hidden="true">
      <path d="M0 150 C 80 200, 220 250, 540 262 L540 320 L0 320 Z" fill="var(--white)"/>
      <path d="M0 162 C 90 215, 230 258, 540 272 L540 320 L0 320 Z" fill="var(--card-black)"/>
      <path d="M0 178 C 100 235, 250 272, 540 286 L540 320 L0 320 Z" fill="var(--red)"/>
      <path d="M0 178 C 100 235, 250 272, 540 286 L540 320 L260 320 C 200 300, 90 260, 0 250 Z" fill="var(--red)"/>
    </svg>

    <div class="person">
      <div class="name">Leo Pemberton-Hale</div>
      <div class="role">Managing Director</div>
    </div>

    <div class="front-mark">
      <div class="brand-name">Fen Athletics</div>
      <div class="tagline">Performance Wear</div>
    </div>

    <ul class="contacts">
      <li>
        <svg viewBox="0 0 24 24" aria-hidden="true"><path d="M6.6 10.8a15.1 15.1 0 0 0 6.6 6.6l2.2-2.2a1 1 0 0 1 1-.25 11.4 11.4 0 0 0 3.6.57 1 1 0 0 1 1 1V20a1 1 0 0 1-1 1A17 17 0 0 1 3 4a1 1 0 0 1 1-1h3.5a1 1 0 0 1 1 1c0 1.25.2 2.45.57 3.57a1 1 0 0 1-.25 1z"/></svg>
        +44 (0)1632 960418
      </li>
      <li>
        <svg viewBox="0 0 24 24" aria-hidden="true"><path d="M2 5h20v14H2z M3.5 6.5 12 13l8.5-6.5" fill="var(--red)"/><path d="M3.5 6.5 12 13l8.5-6.5" fill="none" stroke="var(--card-black)" stroke-width="1.6"/></svg>
        leo@fenathletics.co.uk
      </li>
    </ul>

    <ul class="brand-row" aria-label="Group brands">
      <li><span class="dot"></span>TavaPuni</li>
      <li>ElmStretch</li>
      <li>Fen</li>
      <li>Grit and Rain</li>
    </ul>

    <div class="web"><span class="at">@</span>fenathletics.co.uk</div>

    <address class="address">
      Marsh Lane, Holwell,<br>
      Fenby, FB4 2QT
    </address>
  </section>

</main>
</body>
</html>
```